Kelvara Pane Works Business Card

We need a business card design that is suitable for a Glazing Business. We Specialize in Repairing broken windows and doors and are a 24hr on call service. We manufacture Shower screens, Fly screens, Wardrobe doors, Security doors and grilles + mirrors. We stock a variety of mesh including Standard mesh, Pet resistant mesh, Tressmet & Clearweft. We would like to use a combination of Light Blue, Dark Blue, Black & White with perhaps a picture of glass breaking.

Industry/Entity Type

Business

Contact Information for Business Card

Narooma Glass Service60B Glasshouse Rocks RdNarooma NSW 2546PH / FAX - 02 44765210MOB - 0419682350 Andrewemail - kelvarapane@fenmail.example

Font styles to use
Serif

Colors
34a7d8
0255a3
ffffff

Requirements
Must have
• logo with picture of broken or cracked glass

```html
<!DOCTYPE html>
<html lang="en">
<head>
<meta charset="utf-8">
<title>Kelvara Pane Works – Business Card</title>
<link rel="stylesheet" href="https://fonts.googleapis.com/css2?family=Open+Sans:wght@400;700;800&display=swap">
<style>
  :root {
    --light-blue: #34a7d8;
    --dark-blue: #0255a3;
    --white: #ffffff;
    --card-black: #0c0c0d;
    --card-edge: #1d1e20;
    --text-light: #e9e9e9;
    --rule: #2a2b2e;
    --backdrop: #8f9091;
  }
  * { box-sizing: border-box; margin: 0; padding: 0; }
  html, body {
    width: 1200px; height: 900px; overflow: hidden;
    background: var(--backdrop);
    font-family: "Open Sans", Arial, sans-serif;
  }
  .sheet {
    position: relative; width: 1200px; height: 900px;
    display: flex; flex-direction: column; align-items: center;
    justify-content: center; gap: 24px;
  }
  .card {
    position: relative; width: 700px; height: 400px; overflow: hidden;
    background: radial-gradient(ellipse at 30% 20%, var(--card-edge), var(--card-black) 70%);
  }
  .card__glow {
    position: absolute; border-radius: 50%;
    background: rgba(255,255,255,0.035);
  }
  .card--front .card__glow { width: 330px; height: 330px; right: -60px; bottom: -90px; }
  .card--back .card__glow { width: 330px; height: 330px; left: -120px; top: -20px; }

  .brand { display: flex; align-items: center; gap: 14px; }
  .brand__dot { width: 26px; height: 26px; border-radius: 50%; flex: none; }
  .brand__name {
    font-weight: 800; text-transform: uppercase; letter-spacing: 3px; white-space: nowrap;
  }

  .card--front .brand {
    position: absolute; left: 0; right: 0; top: 160px; justify-content: center;
  }
  .card--front .brand__dot { background: var(--white); }
  .card--front .brand__name { color: var(--white); font-size: 40px; }

  .card--back .brand { position: absolute; right: 40px; top: 70px; }
  .card--back .brand__dot { background: var(--light-blue); }
  .card--back .brand__name { color: var(--light-blue); font-size: 32px; }

  .divider {
    position: absolute; left: 260px; right: 40px; top: 150px;
    height: 1px; background: var(--rule);
  }
  .holder {
    position: absolute; left: 70px; top: 112px;
    color: var(--light-blue); font-weight: 700; font-size: 22px;
  }
  .contact {
    position: absolute; right: 40px; top: 190px; text-align: right;
    color: var(--text-light); font-size: 19px; line-height: 1.3;
  }
  .contact__address { margin-bottom: 14px; }
  .contact__list { list-style: none; }
  .contact__item { display: flex; align-items: center; justify-content: flex-end; gap: 14px; }
  .contact__icon { width: 18px; height: 18px; flex: none; fill: var(--light-blue); }
</style>
</head>
<body>
<main class="sheet">
  <section class="card card--front" aria-label="Card front">
    <div class="card__glow"></div>
    <div class="brand">
      <span class="brand__dot"></span>
      <span class="brand__name">Kelvara Pane Works</span>
    </div>
  </section>

  <section class="card card--back" aria-label="Card back">
    <div class="card__glow"></div>
    <p class="holder">Malcolm</p>
    <div class="brand">
      <span class="brand__dot"></span>
      <span class="brand__name">Kelvara Pane Works</span>
    </div>
    <div class="divider"></div>
    <div class="contact">
      <p class="contact__address">17C Tindale Ridge<br>Rd Tindale NSW 2581</p>
      <ul class="contact__list">
        <li class="contact__item">02 48931067
          <svg class="contact__icon" viewBox="0 0 24 24" aria-label="Phone"><path d="M6.6 10.8a15 15 0 0 0 6.6 6.6l2.2-2.2c.3-.3.7-.4 1-.2 1.1.4 2.3.6 3.6.6.6 0 1 .4 1 1V20c0 .6-.4 1-1 1A17 17 0 0 1 3 4c0-.6.4-1 1-1h3.5c.6 0 1 .4 1 1 0 1.3.2 2.5.6 3.6.1.3 0 .7-.2 1z"/></svg>
        </li>
        <li class="contact__item">02 48931067
          <svg class="contact__icon" viewBox="0 0 24 24" aria-label="Fax"><path d="M6 2h10v5H6zM3 8h18v10h-3v4H6v-4H3zm5 7v5h8v-5zm9-5v2h2v-2z"/></svg>
        </li>
        <li class="contact__item">0419682350
          <svg class="contact__icon" viewBox="0 0 24 24" aria-label="Mobile"><path d="M7 1h10a2 2 0 0 1 2 2v18a2 2 0 0 1-2 2H7a2 2 0 0 1-2-2V3a2 2 0 0 1 2-2zm0 3v14h10V4zm5 15.2a1.2 1.2 0 1 0 0 2.4 1.2 1.2 0 0 0 0-2.4z"/></svg>
        </li>
        <li class="contact__item">kelvarapane@fenmail.example
          <svg class="contact__icon" viewBox="0 0 24 24" aria-label="Email"><path d="M2 5h20v14H2zm2 2v.4l8 5 8-5V7zm0 2.8V17h16V9.8l-8 5z"/></svg>
        </li>
      </ul>
    </div>
  </section>
</main>
</body>
</html>
```